Harbor Ridge Painting Epoxy Flyer

We need a promotional flyer for a new epoxy floor coatings division of our painting company. We do epoxy garage floor coatings and paver sealing. It needs to be based on and very similar to the attached flyer. The garage floor picture needs to look more realistic, and the before and after pavers pictures should look less shiny but still a good contrast. Include attached logo

```html
<!DOCTYPE html>
<html lang="en">
<head>
<meta charset="utf-8">
<title>Harbor Ridge Painting – Epoxy Floor Coatings Flyer</title>
<link href="https://fonts.googleapis.com/css2?family=Anton&family=Montserrat:wght@600;700;800;900&family=Roboto+Condensed:wght@500;700&family=Oswald:wght@600&display=swap" rel="stylesheet">
<style>
  :root {
    --orange: #f7931e;
    --orange-dark: #e0620d;
    --orange-light: #fbb03b;
    --green: #3d8a1b;
    --green-dark: #245e0c;
    --green-light: #8cc63f;
    --ink: #2b2b2b;
    --text: #333333;
    --paper: #ffffff;
    --pave-light: #f1f1f1;
    --pave-mid: #d9d9d9;
    --red: #d9231c;
  }
  * { box-sizing: border-box; margin: 0; padding: 0; }
  html, body { width: 854px; height: 1200px; overflow: hidden; background: #ffffff; }
  .flyer { position: relative; width: 854px; height: 1200px; background: var(--paper); overflow: hidden; font-family: "Roboto Condensed", sans-serif; color: var(--text); }

  .hero-backdrop { position: absolute; left: 0; top: 0; width: 854px; height: 420px;
    background: linear-gradient(180deg, var(--pave-mid) 0%, var(--pave-light) 35%, #ffffff 70%, var(--pave-light) 100%); }

  .brand { position: absolute; top: 98px; left: 0; width: 854px; display: flex; justify-content: center; align-items: center; gap: 10px; }
  .brand-dot { width: 22px; height: 22px; border-radius: 50%; background: var(--green); }
  .brand-name { font-family: "Montserrat", sans-serif; font-weight: 800; font-size: 19px; letter-spacing: 0.5px; color: var(--ink); }

  .headline { position: absolute; left: 0; width: 854px; text-align: center; font-family: "Anton", sans-serif; line-height: 1; text-transform: uppercase; }
  .headline-top { top: 206px; font-size: 76px; color: var(--orange); text-shadow: 0 3px 0 #8a3a06, 0 5px 6px rgba(0,0,0,.25); letter-spacing: 1px; }
  .headline-bottom { top: 280px; font-size: 88px; color: var(--green-light); text-shadow: 0 3px 0 var(--green-dark), 0 5px 6px rgba(0,0,0,.25); letter-spacing: 1px; }

  .compare-band { position: absolute; left: 0; top: 0; }

  .tagline { position: absolute; left: 283px; top: 364px; width: 290px; height: 34px; background: var(--green);
    clip-path: polygon(3% 0, 100% 0, 97% 100%, 0 100%);
    font-family: "Montserrat", sans-serif; font-weight: 700; font-size: 16px; color: #fff;
    display: flex; align-items: center; justify-content: center; }

  .service-col { position: absolute; top: 672px; width: 350px; }
  .service-col.coatings { left: 53px; }
  .service-col.sealing { left: 443px; }
  .col-title { height: 40px; display: flex; align-items: center; justify-content: center;
    font-family: "Montserrat", sans-serif; font-weight: 800; font-size: 20px; color: #fff;
    clip-path: polygon(0 0, 100% 0, 97% 50%, 100% 100%, 0 100%, 3% 50%); }
  .coatings .col-title { background: linear-gradient(180deg, var(--orange-light), var(--orange)); }
  .sealing .col-title { background: linear-gradient(180deg, #4fa324, var(--green)); }
  .benefit-list { list-style: none; margin-top: 8px; }
  .benefit-list li { height: 36px; display: flex; align-items: center; gap: 9px; font-size: 18.5px; font-weight: 500; border-bottom: 1px dashed #8a8a8a; padding-left: 4px; }
  .benefit-list li:last-child { border-bottom: none; }
  .tick { width: 15px; height: 15px; flex: none; }

  .promise-band { position: absolute; left: 0; top: 866px; width: 854px; height: 36px; background: linear-gradient(90deg, var(--orange), var(--orange-light));
    font-family: "Montserrat", sans-serif; font-weight: 800; font-size: 20.5px; color: #fff; display: flex; align-items: center; justify-content: center; }

  .trust-list { position: absolute; left: 53px; top: 922px; list-style: none; }
  .trust-list li { height: 42px; display: flex; align-items: center; gap: 12px; font-size: 18.5px; font-weight: 500; }
  .trust-icon { width: 37px; height: 37px; flex: none; }

  .cta-ribbon { position: absolute; left: 53px; top: 1071px; width: 346px; height: 27px; background: var(--green);
    clip-path: polygon(0 0, 100% 0, 98% 50%, 100% 100%, 0 100%, 2% 50%);
    font-family: "Montserrat", sans-serif; font-weight: 800; font-size: 16px; letter-spacing: 3px; color: #fff;
    display: flex; align-items: center; justify-content: center; }
  .phone { position: absolute; left: 53px; top: 1104px; display: flex; align-items: center; gap: 10px; }
  .phone-icon { width: 34px; height: 34px; }
  .phone-number { font-family: "Montserrat", sans-serif; font-weight: 900; font-size: 43px; color: var(--ink); letter-spacing: -0.5px; }

  .paver-photo { position: absolute; top: 914px; width: 176px; height: 234px; border: 1px solid var(--green); }
  .paver-photo.before { left: 446px; background: linear-gradient(160deg, #6f8f4e 0%, #9a9a9a 18%, #7c7c7c 60%, #5f5f5f 100%); }
  .paver-photo.after { left: 629px; background: linear-gradient(160deg, #7fb34a 0%, #c9878a 14%, #e8e8e8 24%, #dcdcdc 100%); }
  .photo-tag { position: absolute; top: 0; height: 26px; font-family: "Montserrat", sans-serif; font-weight: 800; font-size: 16px; color: #fff; display: flex; align-items: center; }
  .before .photo-tag { right: 0; width: 104px; justify-content: center; background: var(--orange); clip-path: polygon(0 0, 100% 0, 100% 100%, 8% 100%); }
  .after .photo-tag { left: 0; width: 90px; justify-content: center; background: var(--green); clip-path: polygon(0 0, 100% 0, 90% 100%, 0 100%); }

  .service-badge { position: absolute; left: 409px; top: 1037px; width: 120px; height: 120px; border-radius: 50%;
    background: radial-gradient(circle at 50% 35%, #ef3b2c, var(--red)); border: 4px solid #fff; box-shadow: 0 2px 6px rgba(0,0,0,.35);
    display: flex; flex-direction: column; align-items: center; justify-content: center; text-align: center;
    font-family: "Oswald", sans-serif; font-weight: 600; color: #fff; font-size: 13.5px; line-height: 1.05; text-transform: uppercase; }
  .badge-stars { color: #ffd21f; font-size: 12px; letter-spacing: 1px; margin-bottom: 3px; }
</style>
</head>
<body>
<main class="flyer">
  <div class="hero-backdrop" role="img" aria-label="Light grey paver stone surface in soft perspective"></div>

  <div class="brand">
    <span class="brand-dot"></span>
    <span class="brand-name">HARBOR RIDGE PAINTING</span>
  </div>

  <h1>
    <span class="headline headline-top">Upgrade Your</span>
    <span class="headline headline-bottom">Garage &amp; Driveway</span>
  </h1>

  <svg class="compare-band" width="854" height="700" viewBox="0 0 854 700">
    <defs>
      <clipPath id="band-clip"><path d="M0,399 Q427,336 854,399 L854,673 Q427,572 0,673 Z"/></clipPath>
      <linearGradient id="garage-before" x1="0" y1="0" x2="0" y2="1">
        <stop offset="0" stop-color="#c9c6bd"/><stop offset="0.3" stop-color="#8f877a"/><stop offset="1" stop-color="#6f6657"/>
      </linearGradient>
      <linearGradient id="garage-after" x1="0" y1="0" x2="1" y2="1">
        <stop offset="0" stop-color="#b33a36"/><stop offset="0.2" stop-color="#d8d8da"/><stop offset="0.6" stop-color="#b9b4b4"/><stop offset="1" stop-color="#8a8484"/>
      </linearGradient>
    </defs>
    <g clip-path="url(#band-clip)">
      <rect x="0" y="330" width="424" height="350" fill="url(#garage-before)" role="img" aria-label="Worn, stained concrete garage floor before coating"/>
      <rect x="424" y="330" width="6" height="350" fill="#ffffff"/>
      <rect x="430" y="330" width="424" height="350" fill="url(#garage-after)" role="img" aria-label="Glossy, freshly coated epoxy floor after treatment"/>
    </g>
    <path d="M0,399 Q427,336 854,399" fill="none" stroke="#3d8a1b" stroke-width="5"/>
    <path d="M0,673 Q427,572 854,673" fill="none" stroke="#3d8a1b" stroke-width="5"/>
    <polygon points="292,581 424,581 424,614 300,614 306,598" fill="#f7931e"/>
    <text x="412" y="605" text-anchor="end" font-family="Montserrat, sans-serif" font-weight="800" font-size="20" fill="#ffffff">BEFORE</text>
    <polygon points="430,581 530,581 536,598 530,614 430,614" fill="#3d8a1b"/>
    <text x="437" y="605" font-family="Montserrat, sans-serif" font-weight="800" font-size="20" fill="#ffffff">AFTER</text>
  </svg>

  <p class="tagline">From worn-out to like new</p>

  <section class="service-col coatings">
    <h2 class="col-title">EPOXY FLOOR COATINGS</h2>
    <ul class="benefit-list">
      <li><svg class="tick" viewBox="0 0 16 16"><circle cx="8" cy="8" r="8" fill="#f7931e"/><path d="M4.5 8.3l2.3 2.2 4.7-4.8" fill="none" stroke="#fff" stroke-width="1.8"/></svg>Durable, long-lasting finish</li>
      <li><svg class="tick" viewBox="0 0 16 16"><circle cx="8" cy="8" r="8" fill="#f7931e"/><path d="M4.5 8.3l2.3 2.2 4.7-4.8" fill="none" stroke="#fff" stroke-width="1.8"/></svg>Slip-resistant texture</li>
      <li><svg class="tick" viewBox="0 0 16 16"><circle cx="8" cy="8" r="8" fill="#f7931e"/><path d="M4.5 8.3l2.3 2.2 4.7-4.8" fill="none" stroke="#fff" stroke-width="1.8"/></svg>Covers cracks &amp; imperfections</li>
      <li><svg class="tick" viewBox="0 0 16 16"><circle cx="8" cy="8" r="8" fill="#f7931e"/><path d="M4.5 8.3l2.3 2.2 4.7-4.8" fill="none" stroke="#fff" stroke-width="1.8"/></svg>Easy to clean &amp; maintain</li>
    </ul>
  </section>

  <section class="service-col sealing">
    <h2 class="col-title">EPOXY FLOOR COATINGS</h2>
    <ul class="benefit-list">
      <li><svg class="tick" viewBox="0 0 16 16"><circle cx="8" cy="8" r="8" fill="#3d8a1b"/><path d="M4.5 8.3l2.3 2.2 4.7-4.8" fill="none" stroke="#fff" stroke-width="1.8"/></svg>Restores color &amp; enhances appearance</li>
      <li><svg class="tick" viewBox="0 0 16 16"><circle cx="8" cy="8" r="8" fill="#3d8a1b"/><path d="M4.5 8.3l2.3 2.2 4.7-4.8" fill="none" stroke="#fff" stroke-width="1.8"/></svg>Protects from sun fading</li>
      <li><svg class="tick" viewBox="0 0 16 16"><circle cx="8" cy="8" r="8" fill="#3d8a1b"/><path d="M4.5 8.3l2.3 2.2 4.7-4.8" fill="none" stroke="#fff" stroke-width="1.8"/></svg>Helps prevent weeds &amp; sand loss</li>
      <li><svg class="tick" viewBox="0 0 16 16"><circle cx="8" cy="8" r="8" fill="#3d8a1b"/><path d="M4.5 8.3l2.3 2.2 4.7-4.8" fill="none" stroke="#fff" stroke-width="1.8"/></svg>Easier to clean &amp; maintain</li>
    </ul>
  </section>

  <p class="promise-band">PRACTICAL UPGRADES THAT PROTECT AND IMPROVE YOUR HOME</p>

  <ul class="trust-list">
    <li><svg class="trust-icon" viewBox="0 0 38 38"><circle cx="19" cy="19" r="17" fill="#3d8a1b" stroke="#245e0c" stroke-width="3"/><rect x="11" y="11" width="16" height="12" rx="1" fill="none" stroke="#fff" stroke-width="2"/><circle cx="19" cy="26" r="3" fill="#fff"/></svg>Licensed &amp; Insured</li>
    <li><svg class="trust-icon" viewBox="0 0 38 38"><circle cx="19" cy="19" r="17" fill="#3d8a1b" stroke="#245e0c" stroke-width="3"/><rect x="11" y="12" width="16" height="4" fill="#fff"/><rect x="12" y="17" width="14" height="9" fill="none" stroke="#fff" stroke-width="2"/></svg>Family-Owned Local Business</li>
    <li><svg class="trust-icon" viewBox="0 0 38 38"><circle cx="19" cy="19" r="17" fill="#3d8a1b" stroke="#245e0c" stroke-width="3"/><path d="M19 28s-6-6-6-10a6 6 0 0 1 12 0c0 4-6 10-6 10z" fill="#fff"/><circle cx="19" cy="18" r="2.2" fill="#3d8a1b"/></svg>Serving Juniper Flats &amp; Surrounding Areas</li>
  </ul>

  <p class="cta-ribbon">CALL FOR A FREE ESTIMATE</p>
  <div class="phone">
    <svg class="phone-icon" viewBox="0 0 34 34"><circle cx="17" cy="17" r="17" fill="#f7931e"/><path d="M12 9l3 4-2 2c1 3 3 5 6 6l2-2 4 3-2 3c-7 0-13-6-13-13z" fill="#fff"/></svg>
    <span class="phone-number">555-555-0147</span>
  </div>

  <figure class="paver-photo before" role="img" aria-label="Weathered grey paver walkway before sealing">
    <span class="photo-tag">BEFORE</span>
  </figure>
  <figure class="paver-photo after" role="img" aria-label="Clean, sealed light paver walkway with grass edge after sealing">
    <span class="photo-tag">AFTER</span>
  </figure>

  <div class="service-badge">
    <span class="badge-stars">★★★</span>
    Fast,<br>Professional<br>Service<br>You Can<br>Trust
  </div>
</main>
</body>
</html>
```